Brell Stone Company Business Cards

Front and Back Business Card - logo and text setup - cool design. I need workable photoshop or illustrator files so I can setup each employee card with design that is created
Updates

Hi everyone, thank you for the great entries. Please no more white and blue cards - there are so many already - black and silver only now please. thanks!

Target Market(s)

Construction Industry - Facility Managers

Industry/Entity Type

Construction

Contact Information for Business Card

I really like contemporary simplistic looks - clean neat....not opposed to seeing some black backrounds

Requirements
Must have
• Logo/website address with design on front only - www.brellstone-example.com (logo attached)
• Back:
• Name/Title/Company Address/Phone/email address
Nice to have
• Cool design
Should not have
• Nothing gimmicky like Fire or Water - since we are a Fire Protection company - it has all been done

```html
<!DOCTYPE html>
<html lang="en">
<head>
<meta charset="UTF-8">
<title>Brell Stone Company – Business Cards</title>
<link href="https://fonts.googleapis.com/css2?family=Poppins:wght@400;500;700;800&family=Roboto+Condensed:wght@500;700&display=swap" rel="stylesheet">
<style>
  :root {
    --stage: #e9e8e6;
    --card-black: #141416;
    --card-black-raised: #232326;
    --card-silver: #e4e5e8;
    --card-silver-light: #f3f4f6;
    --ink-black: #151517;
    --silver: #b9bcc2;
    --silver-dark: #7d8188;
    --text-grey: #4a4d52;
    --white: #ffffff;
    --shadow: rgba(0, 0, 0, 0.30);
  }
  * { margin: 0; padding: 0; box-sizing: border-box; }
  html, body {
    width: 1200px;
    height: 920px;
    overflow: hidden;
    background: var(--stage);
  }
  .sheet {
    position: relative;
    width: 1200px;
    height: 920px;
  }
  .card {
    position: absolute;
    top: 310px;
    width: 536px;
    height: 300px;
    box-shadow: 0 6px 18px var(--shadow);
  }

  /* Front */
  .card--front {
    left: 46px;
    background: var(--card-black);
  }
  .brand-mark {
    position: absolute;
    left: 0;
    right: 0;
    top: 108px;
    text-align: center;
    font-family: "Poppins", sans-serif;
    font-weight: 800;
    font-size: 52px;
    letter-spacing: -1px;
    color: var(--card-black-raised);
  }
  .front-web {
    position: absolute;
    left: 0;
    right: 0;
    top: 258px;
    text-align: center;
    font-family: "Poppins", sans-serif;
    font-size: 13px;
    letter-spacing: 1px;
    color: var(--white);
  }
  .front-web .domain { color: var(--silver); }

  /* Back */
  .card--back {
    left: 618px;
    background: linear-gradient(135deg, var(--card-silver-light), var(--card-silver));
  }
  .edge-bar {
    position: absolute;
    width: 4px;
    height: 34px;
  }
  .edge-bar--black { background: var(--ink-black); }
  .edge-bar--silver { background: var(--silver-dark); }
  .edge-left { left: 0; }
  .edge-right { right: 0; }
  .edge-top { top: 114px; }
  .edge-bottom { top: 151px; }

  .person {
    position: absolute;
    right: 268px;
    top: 118px;
    text-align: right;
  }
  .person-name {
    font-family: "Roboto Condensed", sans-serif;
    font-weight: 700;
    font-size: 30px;
    color: var(--ink-black);
    line-height: 1;
    white-space: nowrap;
  }
  .person-title {
    margin-top: 10px;
    font-family: "Poppins", sans-serif;
    font-size: 12px;
    color: var(--text-grey);
  }
  .divider {
    position: absolute;
    left: 281px;
    top: 118px;
    width: 2px;
    height: 62px;
    background: var(--silver-dark);
  }
  .contact-list {
    position: absolute;
    left: 295px;
    top: 120px;
    list-style: none;
  }
  .contact-item {
    display: flex;
    align-items: center;
    height: 19px;
    font-family: "Poppins", sans-serif;
    font-size: 13px;
    color: var(--text-grey);
    white-space: nowrap;
  }
  .contact-item svg {
    width: 11px;
    height: 11px;
    margin-right: 10px;
    flex: none;
  }
  .address-line {
    position: absolute;
    left: 0;
    right: 0;
    top: 258px;
    text-align: center;
    font-family: "Poppins", sans-serif;
    font-size: 12px;
    color: var(--text-grey);
    white-space: nowrap;
  }
  .address-line .company {
    font-weight: 700;
    color: var(--ink-black);
    margin-right: 4px;
  }
</style>
</head>
<body>
<main class="sheet">

  <section class="card card--front" aria-label="Card front">
    <div class="brand-mark">Brell Stone</div>
    <div class="front-web">www.<span class="domain">brellstone-example</span>.com</div>
  </section>

  <section class="card card--back" aria-label="Card back">
    <span class="edge-bar edge-bar--black edge-left edge-top"></span>
    <span class="edge-bar edge-bar--silver edge-left edge-bottom"></span>
    <span class="edge-bar edge-bar--black edge-right edge-top"></span>
    <span class="edge-bar edge-bar--silver edge-right edge-bottom"></span>

    <div class="person">
      <div class="person-name">DANA WHITFIELD</div>
      <div class="person-title">Director</div>
    </div>

    <span class="divider"></span>

    <ul class="contact-list">
      <li class="contact-item">
        <svg viewBox="0 0 12 12" aria-hidden="true"><path d="M2.5 1 L4.5 1 L5 3.5 L3.8 4.4 C4.5 6 6 7.5 7.6 8.2 L8.5 7 L11 7.5 L11 9.5 C11 10.3 10.3 11 9.5 11 C5 11 1 7 1 2.5 C1 1.7 1.7 1 2.5 1 Z" fill="var(--silver-dark)"/></svg>
        (555) 014-2290
      </li>
      <li class="contact-item">
        <svg viewBox="0 0 12 12" aria-hidden="true"><rect x="1" y="2.5" width="10" height="7" fill="none" stroke="var(--silver-dark)" stroke-width="1.2"/><path d="M1 2.5 L6 6.5 L11 2.5" fill="none" stroke="var(--silver-dark)" stroke-width="1.2"/></svg>
        info@brellstone-example.com
      </li>
      <li class="contact-item">
        <svg viewBox="0 0 12 12" aria-hidden="true"><circle cx="6" cy="6" r="5" fill="none" stroke="var(--silver-dark)" stroke-width="1.1"/><ellipse cx="6" cy="6" rx="2.2" ry="5" fill="none" stroke="var(--silver-dark)" stroke-width="1"/><path d="M1 6 H11" stroke="var(--silver-dark)" stroke-width="1"/></svg>
        www.brellstone-example.com
      </li>
    </ul>

    <div class="address-line"><span class="company">Brell Stone</span>48 Quarry Lane Millbrook, NY 12545</div>
  </section>

</main>
</body>
</html>
```